BrimFalcon Business Cards

We have a defined brand. Please visit our website to get a feel for the product and the color pallets. www.brimfalcon-example.com

We need an updated, world class business card design. (See the attached existing card design). Please utilize BOTH sides of the card as shown and be creative with the layout. I do want the horse head icon to be positioned as it is with the existing card.

The remainder of the layout can be customized and I also want it vertically oriented.

Attached are the logo files and please use the colors as follows:
Green - #A5CE39
Tan - #CDBD99
Black

Feel free to play with the colors.

```html
<!DOCTYPE html>
<html lang="en">
<head>
<meta charset="utf-8">
<title>BrimFalcon Business Card</title>
<link href="https://fonts.googleapis.com/css2?family=Open+Sans:wght@400;600;700&family=Michroma&display=swap" rel="stylesheet">
<style>
  :root {
    --backdrop: #9b9b9b;
    --card-white: #ffffff;
    --brand-green: #a5ce39;
    --accent-lime: #b9cf2c;
    --deep-green: #3f8f45;
    --ink: #111111;
    --ink-soft: #3a3a3a;
  }
  * { margin: 0; padding: 0; box-sizing: border-box; }
  html, body { width: 1200px; height: 1200px; overflow: hidden; }
  body {
    background: var(--backdrop);
    font-family: "Open Sans", sans-serif;
    color: var(--ink);
    position: relative;
  }
  .card {
    position: absolute;
    border-radius: 15px;
    overflow: hidden;
  }
  .card-front {
    left: 200px; top: 302px; width: 370px; height: 597px;
    background: radial-gradient(ellipse at 55% 50%, #c6d62a 0%, #9cbf36 35%, #6fab3d 75%, var(--deep-green) 100%);
  }
  .front-brand {
    position: absolute;
    left: 0; right: 0; top: 282px;
    display: flex; align-items: center; justify-content: center; gap: 12px;
    font-weight: 700; font-size: 34px; color: var(--ink);
  }
  .brand-dot {
    width: 30px; height: 30px; border-radius: 50%;
    background: var(--ink);
  }
  .card-back {
    left: 600px; top: 305px; width: 363px; height: 589px;
    background: var(--card-white);
  }
  .back-brand {
    position: absolute; left: 43px; top: 122px;
    display: flex; align-items: center; gap: 10px;
  }
  .back-brand .brand-dot { width: 38px; height: 38px; }
  .brand-name { font-weight: 700; font-size: 30px; line-height: 1; color: var(--ink); }
  .tagline {
    position: absolute; left: 93px; top: 159px;
    font-weight: 600; font-size: 11.5px; letter-spacing: 2.6px; color: var(--ink-soft);
  }
  .person-name {
    position: absolute; left: 73px; top: 272px;
    font-family: "Michroma", sans-serif; font-size: 21px; letter-spacing: 6px;
    color: var(--accent-lime);
  }
  .person-title {
    position: absolute; left: 73px; top: 298px;
    font-size: 14.5px; color: var(--ink-soft);
  }
  .contact-icons {
    position: absolute; left: 0; right: 0; top: 362px;
    display: flex; align-items: center; justify-content: center; gap: 4px;
  }
  .rule { width: 33px; height: 1px; background: var(--ink); margin: 0 4px; }
  .icon {
    width: 25px; height: 25px; border-radius: 5px;
    background: var(--accent-lime);
    display: flex; align-items: center; justify-content: center;
  }
  .contact-list {
    position: absolute; left: 0; right: 0; top: 395px;
    text-align: center;
  }
  .phone { font-size: 17.5px; line-height: 21px; }
  .email { font-size: 15px; margin-top: 6px; line-height: 21px; }
  .web { font-size: 15px; line-height: 24px; }
  .divider {
    position: absolute; left: 89px; top: 495px; width: 193px; height: 1px;
    background: var(--ink);
  }
  .address {
    position: absolute; left: 93px; top: 509px;
    font-size: 13px; line-height: 19px;
  }
</style>
</head>
<body>
  <div class="card card-front">
    <div class="front-brand"><span class="brand-dot"></span>BrimFalcon</div>
  </div>

  <div class="card card-back">
    <div class="back-brand"><span class="brand-dot"></span><span class="brand-name">BrimFalcon</span></div>
    <div class="tagline">Performance Driven EVs</div>

    <div class="person-name">JORDAN HALE</div>
    <div class="person-title">CEO/Managing Director</div>

    <div class="contact-icons">
      <span class="rule"></span>
      <span class="icon" aria-label="Phone">
        <svg width="15" height="15" viewBox="0 0 24 24"><path d="M6.6 10.8a15 15 0 0 0 6.6 6.6l2.2-2.2a1 1 0 0 1 1-.25 11.4 11.4 0 0 0 3.6.57 1 1 0 0 1 1 1V20a1 1 0 0 1-1 1A17 17 0 0 1 3 4a1 1 0 0 1 1-1h3.5a1 1 0 0 1 1 1c0 1.25.2 2.45.57 3.57a1 1 0 0 1-.25 1z" fill="#fff"/></svg>
      </span>
      <span class="icon" aria-label="Fax">
        <svg width="15" height="15" viewBox="0 0 24 24"><rect x="6" y="2" width="12" height="6" fill="none" stroke="#fff" stroke-width="2"/><rect x="3" y="8" width="18" height="9" rx="1.5" fill="none" stroke="#fff" stroke-width="2"/><rect x="7" y="14" width="10" height="8" fill="#fff"/></svg>
      </span>
      <span class="icon" aria-label="Email">
        <svg width="16" height="16" viewBox="0 0 24 24"><rect x="2" y="5" width="20" height="14" fill="none" stroke="#fff" stroke-width="2"/><path d="M2 5l10 8 10-8" fill="none" stroke="#fff" stroke-width="2"/></svg>
      </span>
      <span class="icon" aria-label="Website">
        <svg width="16" height="16" viewBox="0 0 24 24" fill="none" stroke="#fff" stroke-width="1.6"><circle cx="12" cy="12" r="9.5"/><ellipse cx="12" cy="12" rx="4.5" ry="9.5"/><path d="M2.5 12h19M4 7h16M4 17h16"/></svg>
      </span>
      <span class="rule"></span>
    </div>

    <div class="contact-list">
      <p class="phone">555-010-2288</p>
      <p class="phone">555-010-2288</p>
      <p class="email">jordan@brimfalcon-example.com</p>
      <p class="web">www.brimfalcon-example.com</p>
    </div>
    <div class="divider"></div>
    <div class="address">
      <p>418 Harbor Lane NW</p>
      <p>Suite 210, Millbrook MI 40100</p>
    </div>
  </div>
</body>
</html>
```